Business Card Design

I already have a company logo for my company. I have a logo for the manufacturer we represent. I want a professional business card design.

```html
<!DOCTYPE html>
<html lang="en">
<head>
<meta charset="utf-8">
<title>Beacon Alert Group – Business Card</title>
<link href="https://fonts.googleapis.com/css2?family=Montserrat:wght@400;500;700;800&display=swap" rel="stylesheet">
<style>
  :root {
    --backdrop: #2c2c2c;
    --card-dark: #111111;
    --card-light: #ffffff;
    --brand-red: #e0242b;
    --text-dark: #222222;
    --text-muted: #3a3a3a;
    --logo-light: #d9d9d9;
  }
  * { box-sizing: border-box; margin: 0; padding: 0; }
  html, body {
    width: 1200px; height: 688px; overflow: hidden;
    background: var(--backdrop);
    font-family: "Montserrat", sans-serif;
  }
  .stage {
    width: 1200px; height: 688px;
    display: flex; align-items: center; justify-content: center; gap: 48px;
  }
  .card {
    width: 520px; height: 298px;
    border-radius: 4px;
    box-shadow: 0 18px 40px rgba(0,0,0,.45);
    position: relative;
  }
  .card-front {
    background: var(--card-dark);
    display: flex; align-items: center; justify-content: center;
  }
  .card-back {
    background: var(--card-light);
    display: flex; align-items: center;
    padding: 0 34px 0 40px;
  }
  .brand {
    display: flex; align-items: center; gap: 12px;
    font-weight: 800; text-transform: uppercase; letter-spacing: .5px;
  }
  .brand-mark { width: 16px; height: 16px; background: var(--brand-red); flex: none; }
  .card-front .brand { color: var(--logo-light); font-size: 26px; }
  .card-back .brand { color: var(--brand-red); font-size: 17px; line-height: 1.15; width: 190px; }
  .divider {
    width: 2px; height: 150px; background: var(--brand-red);
    margin: 0 18px 0 22px; flex: none;
  }
  .contact { color: var(--text-dark); font-size: 11px; line-height: 1.45; }
  .contact-name { color: var(--brand-red); font-size: 20px; font-weight: 700; line-height: 1.1; }
  .contact-role { font-size: 11.5px; font-weight: 500; margin-bottom: 8px; }
  .contact-address { margin-bottom: 8px; color: var(--text-muted); }
  .contact-line { display: flex; align-items: center; gap: 7px; color: var(--text-muted); }
  .contact-line svg { width: 10px; height: 10px; fill: var(--brand-red); flex: none; }
</style>
</head>
<body>
<main class="stage">
  <section class="card card-front" aria-label="Card front">
    <div class="brand"><span class="brand-mark"></span>Beacon Alert Group</div>
  </section>

  <section class="card card-back" aria-label="Card back">
    <div class="brand"><span class="brand-mark"></span>Beacon Alert Group</div>
    <div class="divider"></div>
    <div class="contact">
      <p class="contact-name">Daniel Reyes</p>
      <p class="contact-role">Managing Director</p>
      <p class="contact-address">4820 Larkspur Ave<br>Aurora, CO 80012</p>
      <p class="contact-line">
        <svg viewBox="0 0 10 10" aria-hidden="true"><path d="M2 0.5l2 2-1 1.2c.6 1.3 1.6 2.3 2.8 2.8L7 5.5l2 2-1.2 1.8C4.2 9 1 5.8.7 2.2z"/></svg>
        555.214.0187
      </p>
      <p class="contact-line">
        <svg viewBox="0 0 10 10" aria-hidden="true"><path d="M0 2h10v6H0z M0 2l5 3.5L10 2" /></svg>
        info@beaconalertgroup.com
      </p>
      <p class="contact-line">
        <svg viewBox="0 0 10 10" aria-hidden="true"><circle cx="5" cy="5" r="5"/></svg>
        www.beaconalertgroup.com
      </p>
    </div>
  </section>
</main>
</body>
</html>
```